Cyber Security Site Design (Products & Consulting)

I need my website redesigned to be engaging, clean, efficient and modern. My company (when its up and running) is going to be concentrated on two things: a few specific products for cyber security as well as cyber security consulting services. The background I bring to the field is having worked with small companies all the way to the largest government organizations and advising them on their security posture and how to improve it. We need the ability to add products and services easily.

For a sample product, you can use either Tarnet (http://www.tarnet-relay.org/) or Verodyne Ashmantle (https://www.verodyne.com/products/relay-hx-and-fortified-edge-portal).

It will replace https://lumerafieldworks.com/

Target Market(s)

Cyber Security professionals in all verticals

Coding

Coded - Design and coding required

Number of Pages Required

4 page

Font styles to use
Sans Serif

Colors
6b449b

Requirements
Must have
• Ability to easily modify
• Have main page
• Have product specific pages
• Have consulting services pages
• Have executive team information
• Clean, modern design
• Usage of the logo and its color scheme
Nice to have
• I like the idea of a left collapsed sidebar (so icons only) that can expand for text.
• I am also open to a very unique landing page, possibly a shape in the middle (hexagons maybe?) with each of the options there.
Should not have
• Nothing that looks like it came out of a hacker movie

```html
<!DOCTYPE html>
<html lang="en">
<head>
<meta charset="utf-8">
<title>Lumera Fieldworks — Cyber Security Consulting</title>
<link href="https://fonts.googleapis.com/css2?family=Michroma&family=Jost:wght@400;500;600&display=swap" rel="stylesheet">
<style>
:root{
  --purple:#6b449b;
  --purple-dark:#4f2f78;
  --purple-soft:#7d5aab;
  --ink:#1c1c22;
  --text:#55555c;
  --muted:#8a8a92;
  --grey-band:#ececee;
  --line:#d9d9de;
  --white:#ffffff;
  --footer-bar:#2a2a2e;
}
*{box-sizing:border-box;margin:0;padding:0}
html,body{width:1200px;height:4054px;overflow:hidden;background:var(--white)}
body{font-family:"Jost",sans-serif;color:var(--text);position:relative}
.page{position:relative;width:1200px;height:4054px;overflow:hidden}
.abs{position:absolute}
.center{left:0;width:1200px;text-align:center}
.heading{font-family:"Michroma",sans-serif;color:var(--ink);text-transform:uppercase;letter-spacing:1px;font-weight:400;font-size:21px}

/* header */
.topbar{left:580px;top:0;width:620px;height:38px;background:var(--purple);color:#fff;font-size:15px;display:flex;align-items:center;gap:40px;padding-left:90px}
.topbar span{display:flex;align-items:center;gap:8px}
.brand{display:flex;align-items:center;gap:14px;font-family:"Jost",sans-serif;font-weight:600;color:var(--purple);letter-spacing:1px;white-space:nowrap}
.brand-mark{width:50px;height:50px;background:var(--purple);flex:none}
.header-brand{left:140px;top:50px;font-size:26px}
.header-brand .brand-mark{width:44px;height:44px}
.nav{left:535px;top:38px;height:97px;display:flex;align-items:stretch}
.nav a{font-size:15px;color:var(--ink);text-decoration:none;padding:0 22px;display:flex;align-items:center;letter-spacing:1px;font-weight:500}
.nav a.active{background:var(--purple);color:#fff;margin-top:-38px;padding-top:38px}

/* hero */
.hero{left:0;top:135px;width:1200px;height:562px;background:linear-gradient(180deg,#8a9096 0%,#5d6167 45%,#2e3034 100%)}
.hero-title{top:508px;font-family:"Michroma",sans-serif;color:#fff;font-size:24px;line-height:42px;font-weight:400;letter-spacing:1px}
.btn-hero{left:473px;top:616px;width:251px;height:42px;background:var(--purple);color:#fff;font-size:17px;letter-spacing:1px;display:flex;align-items:center;justify-content:center;gap:10px;border-radius:3px}
.btn-hero i{width:22px;height:22px;border:2px solid #fff;display:block}

/* section divider */
.divider{display:flex;align-items:center;justify-content:center;gap:14px}
.divider b{display:block;width:60px;height:1px;background:var(--muted)}
.divider i{display:block;width:18px;height:18px;border:3px solid var(--purple)}
.intro{font-size:14px;line-height:22px;color:var(--text)}

/* services */
.services-band{left:0;top:697px;width:1200px;height:333px;background:var(--grey-band)}
.service{width:240px;text-align:center}
.service .ring{width:120px;height:120px;border-radius:50%;background:#fff;border:1px solid var(--line);margin:0 auto;display:flex;align-items:center;justify-content:center;box-shadow:0 4px 12px rgba(0,0,0,.06)}
.service .stem{width:1px;height:28px;background:var(--line);margin:0 auto}
.service h3{font-family:"Michroma",sans-serif;font-size:12px;color:var(--ink);font-weight:400;margin-top:14px;letter-spacing:.5px;white-space:nowrap}
.service p{font-size:13px;line-height:17px;margin-top:8px}
.chev{color:var(--ink);font-size:18px;font-weight:600;margin-top:10px;letter-spacing:-3px}

/* team */
.portrait{left:141px;top:1319px;width:300px;height:395px;background:linear-gradient(160deg,#d8d8dc 0%,#b9b9bf 55%,#6a6d74 100%)}
.social{left:141px;top:1719px;width:300px;height:49px;background:#e8e8ea;display:flex;justify-content:center;align-items:center;gap:8px}
.social i{display:block;width:30px;height:30px;border-radius:50%}
.exec-name{left:487px;top:1316px;font-family:"Michroma",sans-serif;font-size:21px;color:var(--ink)}
.exec-role{left:487px;top:1356px;font-size:15px;font-weight:600;color:var(--ink)}
.exec-bio{left:487px;top:1398px;width:573px;font-size:15.5px;line-height:23px;color:var(--text);border-top:1px solid var(--line);padding-top:10px}
.facts{left:487px;top:1525px;width:573px;font-size:14px;color:var(--ink)}
.facts div{height:43px;display:flex;justify-content:space-between;align-items:center;padding:0 20px}
.facts div:nth-child(odd){background:#e9e9ec}
.btn-team{left:643px;top:1725px;width:257px;height:45px;background:#e2e2e5;color:var(--ink);font-size:14px;letter-spacing:1px;display:flex;align-items:center;justify-content:center}

/* products */
.products-band{left:0;top:1873px;width:1200px;height:441px;background:radial-gradient(ellipse at 50% 30%,#3d2a52 0%,#1f1628 55%,#110d16 100%)}
.product{width:433px;height:343px;top:2130px;background:#fff;border-radius:6px;box-shadow:0 6px 20px rgba(0,0,0,.15);text-align:center}
.product .shot{width:200px;height:170px;margin:20px auto 0;border-radius:4px}
.product h3{font-family:"Michroma",sans-serif;font-size:15px;color:var(--ink);font-weight:400;margin-top:26px}
.product p{font-size:15px;line-height:20px;margin-top:12px}

/* about */
.about-title{top:2572px;font-family:"Michroma",sans-serif;font-size:22px;color:var(--ink);font-weight:400}
.about-title span{color:var(--purple);font-family:"Jost",sans-serif;font-size:22px;font-weight:500}
.about-copy{left:140px;top:2680px;width:920px;text-align:center;font-size:16px;line-height:24px}
.about-copy p+p{margin-top:12px}
.connector{left:338px;top:2878px;width:505px;height:1px;background:var(--line)}
.core{left:545px;top:2820px;width:110px;height:110px;border-radius:50%;background:#fff;border:1px solid var(--line);display:flex;align-items:center;justify-content:center;box-shadow:0 4px 12px rgba(0,0,0,.08)}
.core i{width:46px;height:46px;background:var(--purple);display:block}
.pillar{width:220px;text-align:center}
.pillar h4{font-family:"Jost",sans-serif;font-size:16px;color:var(--ink);font-weight:500;letter-spacing:1px;margin-top:10px}
.pillar p{font-size:14px;line-height:18px;margin-top:4px}

/* cta */
.cta{left:0;top:3135px;width:1200px;height:417px;background:linear-gradient(180deg,var(--purple-soft),var(--purple))}
.cta-title{top:3225px;font-family:"Michroma",sans-serif;font-size:22px;line-height:42px;color:#fff;font-weight:400}
.field{background:rgba(255,255,255,.18);color:rgba(255,255,255,.8);font-size:13px;padding:0 14px;display:flex;align-items:center}
.cta-phone{left:770px;top:3330px;font-size:24px;color:#fff}
.cta-note{left:784px;top:3370px;width:240px;font-size:13px;line-height:17px;color:#fff}
.btn-submit{left:784px;top:3425px;width:140px;height:38px;background:#fff;color:var(--purple);font-size:15px;letter-spacing:1px;display:flex;align-items:center;justify-content:center;font-weight:500}

/* footer */
.footer-brand{left:0;width:1200px;top:3636px;justify-content:center;font-size:34px}
.footer-nav{top:3752px;display:flex;justify-content:center;align-items:center;gap:34px;font-size:15px;color:var(--ink);letter-spacing:1px}
.footer-nav i{display:block;width:16px;height:16px;border:1px solid var(--muted)}
.contact{width:300px;text-align:center}
.contact .ico{width:60px;height:60px;margin:0 auto;display:flex;align-items:center;justify-content:center}
.contact .rule{width:210px;height:1px;background:var(--line);margin:-31px auto 28px}
.contact h5{font-size:14px;font-weight:500;color:var(--ink);letter-spacing:1px}
.contact p{font-size:13px;color:var(--text);margin-top:4px}
.copybar{left:0;top:4008px;width:1200px;height:46px;background:var(--footer-bar);color:#d0d0d4;font-size:12px;display:flex;align-items:center;justify-content:center;letter-spacing:1px}
</style>
</head>
<body>
<div class="page">

  <!-- header -->
  <div class="abs topbar">
    <span><svg width="14" height="14" viewBox="0 0 24 24"><path fill="#fff" d="M6.6 10.8a15 15 0 006.6 6.6l2.2-2.2a1 1 0 011-.25 11.4 11.4 0 003.6.57 1 1 0 011 1V20a1 1 0 01-1 1A17 17 0 013 4a1 1 0 011-1h3.5a1 1 0 011 1c0 1.25.2 2.45.57 3.6a1 1 0 01-.25 1z"/></svg>+123 456 8989</span>
    <span><svg width="15" height="12" viewBox="0 0 24 18"><rect x="1" y="1" width="22" height="16" fill="none" stroke="#fff" stroke-width="2"/><path d="M1 1l11 9 11-9" fill="none" stroke="#fff" stroke-width="2"/></svg>inquiry@lumerafieldworks.com</span>
  </div>
  <div class="abs brand header-brand"><span class="brand-mark"></span>LUMERA FIELDWORKS</div>
  <nav class="abs nav">
    <a class="active">HOME</a><a>SERVICES</a><a>OUR TEAM</a><a>PRODUCTS</a><a>CONTACT</a>
  </nav>

  <!-- hero -->
  <div class="abs hero" role="img" aria-label="Photo of three consultants meeting around a laptop in a bright office"></div>
  <h1 class="abs center hero-title">WE PROVIDE EARLY DETECTION, IMMEDIATE<br>REMEDIATION &amp; PROACTIVE PREVENTIVE MEASURES</h1>
  <div class="abs btn-hero"><i></i>CONTACT US TODAY</div>

  <!-- services -->
  <div class="abs services-band"></div>
  <h2 class="abs center heading" style="top:790px">Cyber Security Consulting Services</h2>
  <div class="abs center divider" style="top:843px"><b></b><i></i><b></b></div>
  <p class="abs center intro" style="top:892px">Lorem ipsum dolor sit amet, consectetuer adipiscing elit, sed diam nonummy nibh euismod tincidunt ut laoreet<br>dolore magna aliquam erat volutpat. Ut wisi enim ad minim veniam</p>

  <div class="abs service" style="left:142px;top:972px">
    <div class="ring"><svg width="54" height="54" viewBox="0 0 48 48" fill="none" stroke="#333" stroke-width="1.8"><rect x="6" y="8" width="36" height="24" rx="2"/><path d="M18 40h12M24 32v8"/><path d="M24 13l6 2.5v4.5c0 4-3 6.5-6 7.5-3-1-6-3.5-6-7.5v-4.5z"/><path d="M21 20l2.5 2.5 4-4"/></svg></div>
    <div class="stem"></div>
    <h3>VIRTUAL CISO / VISO</h3>
    <p>Lorem ipsum dolor sit amet,<br>consectetuer adipiscing</p>
    <div class="chev">&rsaquo;&rsaquo;</div>
  </div>
  <div class="abs service" style="left:361px;top:972px">
    <div class="ring"><svg width="54" height="54" viewBox="0 0 48 48" fill="none" stroke="#333" stroke-width="1.8"><path d="M24 6l14 5v11c0 9-6 15-14 19-8-4-14-10-14-19V11z"/><rect x="18" y="21" width="12" height="10" rx="1"/><path d="M20 21v-3a4 4 0 018 0v3"/></svg></div>
    <div class="stem"></div>
    <h3>CYBER SECURITY</h3>
    <p>Lorem ipsum dolor sit amet,<br>consectetuer adipiscing</p>
    <div class="chev">&rsaquo;&rsaquo;</div>
  </div>
  <div class="abs service" style="left:602px;top:972px">
    <div class="ring"><svg width="54" height="54" viewBox="0 0 48 48" fill="none" stroke="#333" stroke-width="1.8"><circle cx="24" cy="12" r="4"/><path d="M17 24a7 7 0 0114 0"/><circle cx="11" cy="30" r="3.5"/><path d="M5 41a6 6 0 0112 0"/><circle cx="37" cy="30" r="3.5"/><path d="M31 41a6 6 0 0112 0"/><path d="M24 24v6M16 28l4-3M32 28l-4-3"/></svg></div>
    <div class="stem"></div>
    <h3>RISK ASSESSMENT</h3>
    <p>Lorem ipsum dolor sit amet,<br>consectetuer adipiscing</p>
    <div class="chev">&rsaquo;&rsaquo;</div>
  </div>
  <div class="abs service" style="left:829px;top:972px">
    <div class="ring"><svg width="54" height="54" viewBox="0 0 48 48" fill="none" stroke="#333" stroke-width="1.8"><circle cx="24" cy="24" r="7"/><circle cx="24" cy="6" r="3"/><circle cx="24" cy="42" r="3"/><circle cx="6" cy="24" r="3"/><circle cx="42" cy="24" r="3"/><circle cx="11" cy="11" r="2.5"/><circle cx="37" cy="11" r="2.5"/><circle cx="11" cy="37" r="2.5"/><circle cx="37" cy="37" r="2.5"/><path d="M24 9v8M24 31v8M9 24h8M31 24h8M13 13l6 6M35 13l-6 6M13 35l6-6M35 35l-6-6"/></svg></div>
    <div class="stem"></div>
    <h3>NETWORK SECURITY</h3>
    <p>Lorem ipsum dolor sit amet,<br>consectetuer adipiscing</p>
    <div class="chev">&rsaquo;&rsaquo;</div>
  </div>

  <!-- executive -->
  <div class="abs portrait" role="img" aria-label="Portrait photo of the founder and CEO in a suit"></div>
  <div class="abs social"><i style="background:#3b5998"></i><i style="background:#1da1f2"></i><i style="background:#0077b5"></i><i style="background:#dd4b39"></i></div>
  <div class="abs exec-name">Daniel Harrow Keswick</div>
  <div class="abs exec-role">Founder &amp; CEO</div>
  <p class="abs exec-bio">Daniel has been in the cyber security fields for over 10 years having worked as a contractor for various Federal agencies. His experiences have provided him the ability to look at the security posture of an organization and provide concise recommendations to improve it's stature.</p>
  <div class="abs facts">
    <div><span>AGE :</span><span>48</span></div>
    <div><span>LOCATION :</span><span>Marlow / Dunmore, NC, USA</span></div>
    <div><span>EXPERIENCE :</span><span>10 Years</span></div>
    <div><span>PHONE :</span><span>123 456 7890</span></div>
  </div>
  <div class="abs btn-team">VIEW ALL TEAM MEMBERS</div>

  <!-- products -->
  <div class="abs products-band"></div>
  <h2 class="abs center heading" style="top:1962px;color:#fff">Cyber Security Consulting Products</h2>
  <div class="abs center divider" style="top:2015px"><b style="background:#aaa"></b><i style="border-color:#fff"></i><b style="background:#aaa"></b></div>
  <p class="abs center intro" style="top:2060px;color:#e3dcec">Lorem ipsum dolor sit amet, consectetuer adipiscing elit, sed diam nonummy nibh euismod tincidunt ut laoreet<br>dolore magna aliquam erat volutpat. Ut wisi enim ad minim veniam</p>

  <div class="abs product" style="left:141px">
    <div class="shot" role="img" aria-label="Product box with software disc" style="background:linear-gradient(150deg,#fff3b0,#f2c21a 60%,#c99a08)"></div>
    <h3>PRODUCT 1</h3>
    <p>Lorem ipsum dolor sit amet, consectetuer adipis<br>cing elit, sed diam nonummy nibh euismod</p>
    <div class="chev">&rsaquo;&rsaquo;</div>
  </div>
  <div class="abs product" style="left:624px">
    <div class="shot" role="img" aria-label="Product box with software disc" style="background:linear-gradient(150deg,#d8f0ff,#4aa8e6 60%,#1f6fb0)"></div>
    <h3>PRODUCT 2</h3>
    <p>Lorem ipsum dolor sit amet, consectetuer adipis<br>cing elit, sed diam nonummy nibh euismod</p>
    <div class="chev">&rsaquo;&rsaquo;</div>
  </div>

  <!-- about -->
  <h2 class="abs center about-title">ABOUT LUMERA <span>FIELDWORKS</span></h2>
  <div class="abs center divider" style="top:2626px"><b></b><i></i><b></b></div>
  <div class="abs about-copy">
    <p>We are a company that takes its roots from the idea of providing appropriate and creative solutions for cyber security operations, development and management. We have a mission first mindset for our clients and their objectives.</p>
    <p>We are located in the Marlow / Dunmore, NC, USA area but are able to work with clients world-wide. Please contact us for any inquires you may have and we will be glad to assist you in any way possible.</p>
  </div>
  <div class="abs connector"></div>
  <div class="abs core"><i></i></div>
  <div class="abs pillar" style="left:228px;top:2845px">
    <svg width="60" height="60" viewBox="0 0 48 48"><path d="M4 44L24 14l20 30z" fill="#2a2a30"/><path d="M24 14V4" stroke="#2a2a30" stroke-width="2"/><path d="M24 4h11l-3 4 3 4H24z" fill="#6b449b"/></svg>
    <h4>MISSION</h4>
    <p>Lorem ipsum dolor sit<br>amet, consectetuer adipis</p>
    <div class="chev">&rsaquo;&rsaquo;</div>
  </div>
  <div class="abs pillar" style="left:733px;top:2845px">
    <svg width="60" height="60" viewBox="0 0 48 48"><circle cx="24" cy="24" r="20" fill="none" stroke="#2a2a30" stroke-width="2"/><path d="M8 24c5-8 11-11 16-11s11 3 16 11c-5 8-11 11-16 11S13 32 8 24z" fill="#2a2a30"/><circle cx="24" cy="24" r="6" fill="#6b449b"/></svg>
    <h4>VISION</h4>
    <p>Lorem ipsum dolor sit<br>amet, consectetuer adipis</p>
    <div class="chev">&rsaquo;&rsaquo;</div>
  </div>

  <!-- call to action -->
  <div class="abs cta"></div>
  <h2 class="abs center cta-title">WE PROVIDE SECURITY SERVICES THAT MATCHES YOUR<br>NEEDS &amp; YOUR BUDGET!</h2>
  <div class="abs field" style="left:162px;top:3325px;width:262px;height:38px">Name</div>
  <div class="abs field" style="left:162px;top:3373px;width:262px;height:38px">Phone</div>
  <div class="abs field" style="left:162px;top:3421px;width:262px;height:38px">Email</div>
  <div class="abs field" style="left:435px;top:3325px;width:262px;height:38px">Interested in</div>
  <div class="abs field" style="left:435px;top:3373px;width:262px;height:86px;align-items:flex-start;padding-top:10px">Enter Your Word</div>
  <div class="abs cta-phone">+ 123 456 7890</div>
  <p class="abs cta-note">Lorem ipsum dolor sit amet, consectet adipiscing, sed diam tetuer adi</p>
  <div class="abs btn-submit">SUBMIT</div>

  <!-- footer -->
  <div class="abs brand footer-brand"><span class="brand-mark"></span>LUMERA FIELDWORKS</div>
  <div class="abs center footer-nav"><span>HOME</span><i></i><span>SERVICES</span><i></i><span>OUR TEAM</span><i></i><span>PRODUCTS</span><i></i><span>CONTACT</span></div>

  <div class="abs contact" style="left:163px;top:3800px">
    <div class="ico"><svg width="44" height="44" viewBox="0 0 48 48" fill="none" stroke="#2a2a30" stroke-width="2.5"><rect x="6" y="6" width="36" height="36" rx="8"/><path d="M24 36s-8-8-8-14a8 8 0 0116 0c0 6-8 14-8 14z"/><circle cx="24" cy="22" r="3"/></svg></div>
    <div class="rule"></div>
    <h5>ADDRESS</h5>
    <p>Marlow / Dunmore, NC, USA</p>
  </div>
  <div class="abs contact" style="left:450px;top:3800px">
    <div class="ico"><svg width="44" height="44" viewBox="0 0 48 48" fill="none" stroke="#2a2a30" stroke-width="2.5"><rect x="6" y="6" width="36" height="36" rx="8"/><path d="M18 14h4l2 6-3 2a12 12 0 006 6l2-3 6 2v4a2 2 0 01-2 2A18 18 0 0116 16a2 2 0 012-2z"/></svg></div>
    <div class="rule"></div>
    <h5>PHONE</h5>
    <p>+ 123 456 7890</p>
  </div>
  <div class="abs contact" style="left:737px;top:3800px">
    <div class="ico"><svg width="44" height="44" viewBox="0 0 48 48" fill="none" stroke="#2a2a30" stroke-width="2.5"><rect x="6" y="6" width="36" height="36" rx="8"/><rect x="14" y="16" width="20" height="15"/><path d="M14 16l10 8 10-8"/></svg></div>
    <div class="rule"></div>
    <h5>EMAIL</h5>
    <p>info@lumerafieldworks.com</p>
  </div>

  <div class="abs copybar">COPYRIGHT © 2018 LUMERA FIELDWORKS . ALL RIGHTS RESERVED.</div>
</div>
</body>
</html>
```